Beacon Advisory Website

I currently have a website www.beaconadvisoryinc.com. We are a IT Consulting Company. Our website will pretty much tell out our services. I am looking to enhance my website and make it look more professional. Looking for very classy and Contemporary look and design for my website.

It Company

```html
<!DOCTYPE html>
<html lang="en">
<head>
<meta charset="utf-8">
<title>Beacon Advisory</title>
<link href="https://fonts.googleapis.com/css2?family=Lato:wght@400;700;900&display=swap" rel="stylesheet">
<style>
:root{
  --sky:#0a9bd7;
  --navy:#1d4289;
  --navy-deep:#153a7a;
  --social:#1a5aa6;
  --nav-bg:#333333;
  --nav-line:#4a4a4a;
  --ink:#2b2b2b;
  --text:#333333;
  --muted:#c8c8c8;
  --white:#ffffff;
  --footer:#333333;
}
*{box-sizing:border-box;margin:0;padding:0}
html,body{width:1147px;height:1200px;overflow:hidden}
body{position:relative;background:var(--white);font-family:'Lato',sans-serif;color:var(--text)}
.topbar{position:absolute;left:0;top:0;width:1147px;height:33px;background:var(--sky)}
.topbar .socials{position:absolute;left:914px;top:0;display:flex}
.topbar .socials span{width:35px;height:33px;background:var(--social);border-left:1px solid #3b78c0;display:block;position:relative}
.topbar .socials span::after{content:"";position:absolute;left:12px;top:11px;width:11px;height:11px;border-radius:2px;background:var(--white)}
.header{position:absolute;left:0;top:33px;width:1147px;height:82px}
.brand{position:absolute;left:94px;top:22px;display:flex;align-items:center;gap:10px}
.brand .mark{width:38px;height:38px;border-radius:50%;background:var(--navy)}
.brand .name{font-size:22px;font-weight:900;color:var(--navy);letter-spacing:.5px}
.phone{position:absolute;right:95px;top:30px;display:flex;align-items:center;gap:6px;font-size:17px;font-weight:700;color:var(--ink)}
.nav{position:absolute;left:0;top:115px;width:1147px;height:41px;background:var(--nav-bg)}
.nav ul{list-style:none;position:absolute;left:94px;top:0;display:flex;height:41px}
.nav li{height:41px;line-height:41px;text-align:center;color:var(--white);font-size:15px;font-weight:700;border-right:1px solid var(--nav-line);position:relative}
.nav li:last-child{border-right:0}
.nav li.active{background:var(--sky)}
.nav li.active::after{content:"";position:absolute;left:50%;bottom:0;margin-left:-6px;border:6px solid transparent;border-bottom-color:var(--white);border-top:0}
.hero{position:absolute;left:0;top:156px;width:1147px;height:451px;background:linear-gradient(180deg,#8ea4ba 0%,#b7b8ae 30%,#c49a63 55%,#6b5a3d 68%,#2f3b2c 75%)}
.hero .band{position:absolute;left:0;top:276px;width:1147px;height:175px;background:rgba(26,70,145,.88)}
.hero h1{position:absolute;left:0;top:292px;width:1147px;text-align:center;color:var(--white);font-size:29px;font-weight:900}
.hero .rule{position:absolute;left:250px;top:342px;width:647px;height:1px;background:rgba(255,255,255,.6)}
.hero .rule::after{content:"";position:absolute;left:50%;top:0;margin-left:-9px;border:9px solid transparent;border-top:9px solid var(--white);border-bottom:0}
.hero p{position:absolute;left:100px;top:361px;width:947px;text-align:center;color:var(--white);font-size:12px;font-weight:700;line-height:18.5px}
.hero .more{position:absolute;left:555px;top:430px;width:37px;height:21px;background:var(--white);border-radius:3px 3px 0 0;color:#555;font-size:20px;line-height:22px;text-align:center}
.card{position:absolute;top:650px;width:295px;height:352px;border:1px solid #e3e3e3;border-top:3px solid var(--navy);background:var(--white);box-shadow:0 10px 14px -10px rgba(0,0,0,.18)}
.card h2{position:absolute;left:63px;top:18px;font-size:25px;font-weight:700;color:var(--ink);white-space:nowrap}
.card h2 em{font-style:normal;color:var(--navy)}
.card .badge{position:absolute;left:13px;top:15px;width:37px;height:37px;border-radius:50%;background:var(--ink)}
.card .badge::after{content:"";position:absolute;left:12px;top:12px;width:13px;height:13px;border:2px solid var(--white);border-radius:50%}
.card .photo{position:absolute;left:13px;top:67px;width:268px;height:117px;border:1px solid #ddd}
.card p{position:absolute;left:13px;width:274px;font-size:11.3px;line-height:17.2px;color:var(--text)}
.card .plus{position:absolute;right:-1px;bottom:-1px;width:25px;height:25px;background:var(--navy);color:var(--white);font-size:22px;font-weight:700;line-height:24px;text-align:center}
.services{position:absolute;left:12px;top:172px;list-style:none;width:215px}
.services li{height:32px;border-bottom:1px dotted #999;display:flex;align-items:center;gap:12px;font-size:13px;color:var(--ink)}
.services li:last-child{border-bottom:0}
.services svg{flex:none}
.footer{position:absolute;left:0;top:1058px;width:1147px;height:142px;background:var(--footer);border-top:2px solid #222}
.footer .links{position:absolute;left:96px;top:33px;color:var(--white);font-size:13px;word-spacing:2px}
.footer .links span{color:var(--muted);margin:0 5px}
.newsletter{position:absolute;left:95px;top:80px;display:flex;align-items:center}
.newsletter .env{width:37px;height:37px;border-radius:50%;border:2px solid var(--white);background:var(--footer);position:relative;z-index:1}
.newsletter .env svg{position:absolute;left:8px;top:10px}
.newsletter .field{margin-left:-8px;width:172px;height:37px;background:var(--white);border-radius:0 3px 3px 0;padding-left:20px;line-height:37px;font-size:12px;color:#777}
.newsletter .btn{margin-left:9px;width:98px;height:37px;background:var(--navy-deep);border-radius:3px;color:var(--white);font-size:14px;font-weight:700;line-height:37px;text-align:center}
.footer .round{position:absolute;top:83px;display:flex;gap:9px;left:429px}
.footer .round span{width:25px;height:25px;border-radius:50%;background:var(--white);display:block}
.footer .brand-foot{position:absolute;left:845px;top:40px;display:flex;align-items:center;gap:8px}
.footer .brand-foot .mark{width:34px;height:34px;border-radius:50%;background:#8a8a8a}
.footer .brand-foot .name{font-size:20px;font-weight:900;color:#a8a8a8}
.footer .copy{position:absolute;right:97px;top:104px;color:var(--white);font-size:12px}
</style>
</head>
<body>
<div class="topbar"><div class="socials"><span></span><span></span><span></span><span></span></div></div>

<header class="header">
  <div class="brand"><span class="mark"></span><span class="name">Beacon Advisory</span></div>
  <div class="phone">
    <svg width="24" height="24" viewBox="0 0 24 24"><circle cx="12" cy="12" r="11" fill="none" stroke="#1d4289" stroke-width="1.8"/><path d="M8.5 6.5c-1 1-1 3 .8 5.6s4 4.2 5.5 4.3c1 .1 1.8-.6 2-1.2l-2-1.6-1.2.9c-1-.4-2.6-2-3-3l.9-1.2-1.6-2z" fill="#1d4289"/></svg>
    555 014 2290
  </div>
</header>

<nav class="nav">
  <ul>
    <li class="active" style="width:167px">COMPANY</li>
    <li style="width:157px">SERVICES</li>
    <li style="width:174px">SOLUTIONS</li>
    <li style="width:174px">RESOURCES</li>
    <li style="width:147px">CAREER</li>
    <li style="width:141px">CONTACT US</li>
  </ul>
</nav>

<section class="hero" role="img" aria-label="Photo of an elephant walking along a road toward the viewer at sunset, trees on either side">
  <div class="band"></div>
  <h1>WELCOME TO BEACON ADVISORY</h1>
  <div class="rule"></div>
  <p>Today's IT market is a dynamic, fast-paced industry, with ever-increasing demands. Meeting these demands for over 25 years, Beacon Advisory maintains a global presence, aggressively recruiting expertly qualified IT and Management Professionals from around the world and cultivating key partnerships with corporations to understand their business models end-to-end, with a goal of delivering exceptional client service and ensuring a consistent delivery of the talent needed to drive results.</p>
  <div class="more">+</div>
</section>

<article class="card" style="left:94px">
  <span class="badge"></span>
  <h2><em>IT</em> CONSULTING</h2>
  <div class="photo" role="img" aria-label="Photo of a businesswoman working on a laptop in a bright office" style="background:linear-gradient(90deg,#8aa0c4 0%,#dfe6ee 45%,#cfd8cf 75%,#b8cbb0 100%)"></div>
  <p style="top:202px">Information technology should improve business results. Northwind helps companies make sure it does. We look at IT issues strategically, in the broader context of our clients' business. Our experts provide an objective, independent perspective to help companies realize the full potential of their IT resources, investments and assets.</p>
  <span class="plus">+</span>
</article>

<article class="card" style="left:430px">
  <span class="badge"></span>
  <h2><em>WHAT</em> WE DO</h2>
  <p style="top:69px">We are successful in deploying all students we trained into project with 2-3 weeks after training program. Our training programs will last for 6-8 weeks dependents on technology. We will provide on job support for trainees until technology comfort level is attained.</p>
  <ul class="services">
    <li><svg width="18" height="18" viewBox="0 0 18 18"><circle cx="9" cy="9" r="6" fill="none" stroke="#1d4289" stroke-width="2"/><circle cx="9" cy="9" r="2" fill="#1d4289"/></svg>Technology</li>
    <li><svg width="18" height="18" viewBox="0 0 18 18"><rect x="3" y="3" width="12" height="12" fill="none" stroke="#1d4289" stroke-width="2"/></svg>Offshore Business</li>
    <li><svg width="18" height="18" viewBox="0 0 18 18"><rect x="4" y="2" width="10" height="14" rx="2" fill="none" stroke="#1d4289" stroke-width="2"/></svg>Application Developement</li>
    <li><svg width="18" height="18" viewBox="0 0 18 18"><circle cx="9" cy="5" r="3" fill="none" stroke="#1d4289" stroke-width="1.6"/><circle cx="5" cy="12" r="3" fill="none" stroke="#1d4289" stroke-width="1.6"/><circle cx="13" cy="12" r="3" fill="none" stroke="#1d4289" stroke-width="1.6"/></svg>Enterprise Integration</li>
    <li><svg width="18" height="18" viewBox="0 0 18 18"><circle cx="9" cy="9" r="6" fill="none" stroke="#1d4289" stroke-width="2" stroke-dasharray="3 2"/><circle cx="9" cy="9" r="2.5" fill="#1d4289"/></svg>IT Consulting</li>
  </ul>
  <span class="plus">+</span>
</article>

<article class="card" style="left:760px">
  <span class="badge"></span>
  <h2><em>OFF</em>SHORE</h2>
  <div class="photo" role="img" aria-label="Illustration of a blue world map with glowing network connection lines" style="background:linear-gradient(135deg,#1b4f8a 0%,#3a8cc8 50%,#7fc4ea 100%)"></div>
  <p style="top:202px">Our Offshore development model has a unique distinction of providing efficient software solutions with cost and quality advantage, using state-of-the-art technologies, having the capacity to handle large projects and, above all, the ability to execute timely deliveries.</p>
  <span class="plus">+</span>
</article>

<footer class="footer">
  <div class="links">COMPANY<span>/</span>SERVICES<span>/</span>SOLUTIONS<span>/</span>RESOURCES<span>/</span>CAREER<span>/</span>CONTACT US</div>
  <div class="newsletter">
    <div class="env"><svg width="17" height="13" viewBox="0 0 17 13"><rect x="1" y="1" width="15" height="11" fill="none" stroke="#fff" stroke-width="1.5"/><path d="M1 1l7.5 6L16 1" fill="none" stroke="#fff" stroke-width="1.5"/></svg></div>
    <div class="field">Sign Up for Newsletter</div>
    <div class="btn">SUBSCRIBE</div>
  </div>
  <div class="round"><span></span><span></span><span></span><span></span></div>
  <div class="brand-foot"><span class="mark"></span><span class="name">Beacon Advisory</span></div>
  <div class="copy">© 2016 BeaconAdvisory. All Right Reserved.</div>
</footer>
</body>
</html>
```